Velk Partners Building Business Cards

We need a business card that reflects our business as "Solar Experts" in San Diego. Browse our website www.velkpartners.example our License needs to be displayed as "CSLB# 3867140" our phone number is (619) 555-0187

Save thousands on your electric bills and increase the value of your home while helping to protect the environment. Our solar installation experts will help you design the system that's right for you, using only the highest quality equipment that will look great and give you ideal performance. Our goal is to make you energy independent, and get your electric bill to 0.

Paul Osterby
(619) 555-0187
paul@velkpartners.example

Target Market(s)

Home owners in san diego looking for solar

Industry/Entity Type

Solar Energy

Contact Information for Business Card

Paul Osterby
(619) 555-0187
paul@velkpartners.example

Font styles to use
Other font styles liked:
• Use our logo font

Requirements
Must have
• License needs to be displayed as "CSLB# 3867140" our phone number is (619) 555-0187
Nice to have
• Real images of rooftop home solar in san diego
Should not have
• our business address

```html
<!DOCTYPE html>
<html lang="en">
<head>
<meta charset="utf-8">
<title>Velk Partners Building – Business Cards</title>
<link href="https://fonts.googleapis.com/css2?family=Montserrat:wght@800&family=Open+Sans:wght@400;600&display=swap" rel="stylesheet">
<style>
  :root {
    --navy: #1a3a72;
    --sun: #f5a800;
    --paper: #ffffff;
    --ink: #3a3a3a;
    --rule: #d4d4d4;
    --backdrop: #e9ecec;
  }
  * { margin: 0; padding: 0; box-sizing: border-box; }
  html, body { width: 1200px; height: 812px; overflow: hidden; }
  body {
    background: var(--backdrop);
    font-family: "Open Sans", Arial, sans-serif;
    position: relative;
  }
  .card {
    position: absolute;
    top: 252px;
    width: 540px;
    height: 309px;
    box-shadow: 0 6px 18px rgba(0,0,0,0.18);
    overflow: hidden;
  }
  .card--back { left: 40px; background: var(--navy); }
  .card--front { left: 620px; background: var(--paper); }

  /* back side */
  .back-brand {
    position: absolute;
    left: 0; right: 0; top: 112px;
    display: flex; align-items: center; justify-content: center; gap: 12px;
  }
  .back-brand__dot {
    width: 26px; height: 26px; border-radius: 50%; background: var(--sun);
  }
  .back-brand__name {
    font-family: "Montserrat", Arial, sans-serif;
    font-weight: 800;
    font-size: 28px;
    color: var(--paper);
  }
  .back-web {
    position: absolute;
    left: 0; right: 0; top: 222px;
    text-align: center;
    color: var(--paper);
    font-size: 13px;
    letter-spacing: 2.5px;
  }

  /* front side */
  .roof { position: absolute; inset: 0; width: 540px; height: 309px; }
  .front-brand {
    position: absolute;
    left: 40px; top: 176px;
    width: 250px;
    font-family: "Montserrat", Arial, sans-serif;
    font-weight: 800;
    font-size: 28px;
    line-height: 1.12;
    color: var(--navy);
  }
  .divider {
    position: absolute;
    left: 318px; top: 104px;
    width: 1px; height: 150px;
    background: var(--rule);
  }
  .contact {
    position: absolute;
    left: 338px; top: 106px;
    width: 196px;
    color: var(--ink);
  }
  .contact__name {
    font-family: "Montserrat", Arial, sans-serif;
    font-weight: 800;
    font-size: 20px;
    color: var(--navy);
    line-height: 1.1;
  }
  .contact__title {
    font-size: 14px;
    color: var(--sun);
    margin-bottom: 10px;
  }
  .contact__license { font-size: 13px; margin-bottom: 10px; }
  .contact__list { list-style: none; font-size: 12.5px; }
  .contact__list li { display: flex; align-items: center; gap: 7px; line-height: 1.55; white-space: nowrap; }
  .contact__icon { width: 11px; height: 11px; flex: none; fill: var(--navy); }
</style>
</head>
<body>

<section class="card card--back" aria-label="Business card back">
  <div class="back-brand">
    <span class="back-brand__dot"></span>
    <span class="back-brand__name">Velk Partners Building</span>
  </div>
  <p class="back-web">WWW.VELKPARTNERS.EXAMPLE</p>
</section>

<section class="card card--front" aria-label="Business card front">
  <svg class="roof" viewBox="0 0 540 309" aria-hidden="true">
    <polygon points="0,0 540,0 540,95 289,12 0,108" fill="var(--navy)"/>
    <polyline points="0,112 289,18 540,100" fill="none" stroke="var(--sun)" stroke-width="5"/>
    <polygon points="0,118 289,24 540,106 540,309 0,309" fill="var(--paper)"/>
  </svg>

  <div class="front-brand">Velk Partners<br>Building</div>

  <div class="divider"></div>

  <div class="contact">
    <p class="contact__name">Paul Osterby</p>
    <p class="contact__title">CEO/Founder</p>
    <p class="contact__license">CSLB# 3867140</p>
    <ul class="contact__list">
      <li>
        <svg class="contact__icon" viewBox="0 0 24 24"><path d="M6.6 10.8a15.1 15.1 0 0 0 6.6 6.6l2.2-2.2a1 1 0 0 1 1-.25 11.4 11.4 0 0 0 3.6.6 1 1 0 0 1 1 1V20a1 1 0 0 1-1 1A17 17 0 0 1 3 4a1 1 0 0 1 1-1h3.5a1 1 0 0 1 1 1c0 1.25.2 2.45.6 3.6a1 1 0 0 1-.25 1z"/></svg>
        (619) 555-0187
      </li>
      <li>
        <svg class="contact__icon" viewBox="0 0 24 24"><path d="M2 5h20v14H2z M2 5l10 8 10-8" stroke="#fff" stroke-width="1.5"/></svg>
        paul@velkpartners.example
      </li>
      <li>
        <svg class="contact__icon" viewBox="0 0 24 24"><circle cx="12" cy="12" r="11"/><path d="M2 12h20M12 1c3 3 3 19 0 22M12 1c-3 3-3 19 0 22" stroke="#fff" stroke-width="1.5" fill="none"/></svg>
        www.velkpartners.example
      </li>
    </ul>
  </div>
</section>

</body>
</html>
```